Simple and clean

We need a business card design for a new company called Dwelling Hawk. It is a search engine to find current properties for sale or rent in New Zealand market.
We have already a colour scheme that we would like people to use.
Light brown: #D4CCB0
Light green: #D6E4D4
Green: #669966
Black/White
It is OK to divert from this colour scheme slightly as long as there is a green component to the business card.
Final design should be clean, simple and should communicate the nature of the business.
Target Market(s)
- First home buyers
- Real estate agents
- People seeking rentals
Industry/Entity Type
Business
Requirements
Must have
- Use those or similar colours.
Light brown: #D4CCB0
Light green: #D6E4D4
Green: #669966
Black/White

```html
<!DOCTYPE html>
<html lang="en">
<head>
<meta charset="utf-8">
<title>Dwelling Hawk – Business Card</title>
<link rel="stylesheet" href="https://fonts.googleapis.com/css2?family=Open+Sans:wght@700&family=Arimo:wght@400&display=swap">
<style>
  :root {
    --ink: #000000;
    --paper: #ffffff;
    --green: #669966;
    --light-green: #D6E4D4;
    --light-brown: #D4CCB0;
    --page: #ffffff;
  }
  * { margin: 0; padding: 0; box-sizing: border-box; }
  html, body {
    width: 1200px;
    height: 900px;
    overflow: hidden;
    background: var(--page);
  }
  .canvas {
    position: relative;
    width: 1200px;
    height: 900px;
  }
  .business-card {
    position: absolute;
    left: 170px;
    top: 200px;
    width: 860px;
    height: 500px;
    background: var(--paper);
    box-shadow: 0 6px 16px rgba(0,0,0,0.35);
  }
  .card-face {
    position: absolute;
    left: 0; top: 0;
    width: 860px;
    height: 440px;
    background: var(--ink);
  }
  .brand {
    position: absolute;
    left: 48px;
    top: 196px;
    display: flex;
    align-items: center;
    gap: 14px;
  }
  .brand-dot {
    width: 26px;
    height: 26px;
    border-radius: 50%;
    background: var(--green);
  }
  .brand-name {
    font-family: "Open Sans", sans-serif;
    font-weight: 700;
    font-size: 40px;
    line-height: 1;
    color: var(--light-green);
    white-space: nowrap;
  }
  .divider {
    position: absolute;
    left: 462px;
    top: 18px;
    width: 4px;
    height: 400px;
  }
  .contact {
    position: absolute;
    left: 504px;
    top: 66px;
  }
  .contact-name,
  .contact-role {
    font-family: "Open Sans", sans-serif;
    font-weight: 700;
    color: var(--green);
    line-height: 1;
  }
  .contact-name { font-size: 34px; }
  .contact-role { font-size: 26px; margin-top: 2px; }
  .contact-details {
    margin-top: 34px;
    font-family: "Arimo", sans-serif;
    font-size: 23px;
    line-height: 1.1;
    color: var(--paper);
  }
  .contact-web {
    margin-top: 34px;
    font-family: "Arimo", sans-serif;
    font-size: 23px;
    color: var(--paper);
  }
  .footer-band {
    position: absolute;
    left: 0;
    top: 440px;
    width: 860px;
    height: 60px;
    display: flex;
    align-items: center;
    justify-content: center;
    font-family: "Open Sans", sans-serif;
    font-weight: 700;
    font-size: 19px;
    letter-spacing: 0.32em;
    color: var(--ink);
  }
</style>
</head>
<body>
<main class="canvas">
  <article class="business-card">
    <div class="card-face">
      <div class="brand">
        <span class="brand-dot"></span>
        <span class="brand-name">Dwelling Hawk</span>
      </div>
      <svg class="divider" viewBox="0 0 4 400" preserveAspectRatio="none" aria-hidden="true">
        <defs>
          <linearGradient id="divider-fade" x1="0" y1="0" x2="0" y2="1">
            <stop offset="0" stop-color="#ffffff" stop-opacity="0"/>
            <stop offset="0.35" stop-color="#ffffff" stop-opacity="0.95"/>
            <stop offset="0.6" stop-color="#ffffff" stop-opacity="0.8"/>
            <stop offset="1" stop-color="#ffffff" stop-opacity="0"/>
          </linearGradient>
        </defs>
        <rect x="1" y="0" width="2" height="400" fill="url(#divider-fade)"/>
      </svg>
      <div class="contact">
        <p class="contact-name">Sam Carter</p>
        <p class="contact-role">Director</p>
        <p class="contact-details">Mobile number<br>Email address</p>
        <p class="contact-web">www.dwellinghawk.co.nz</p>
      </div>
    </div>
    <div class="footer-band">www.dwellinghawk.co.nz</div>
  </article>
</main>
</body>
</html>
```